Brindlewick Cellars Winery… For non-interventionist winemakers, wine-making begins in the

Need a new website for my new winery…previous one lost in divorce to my cheating ex wife…sigh. Calling it Brindlewick Cellars. Want it to look like a wedding sight…calligraphy writing…black and white…with some black roses…want the look of a invitational wedding site…celebratory! We employ a combination of modern techniques and old world traditions, practicing both the cuvee and "field blending" methods, to create a range of distinctive varietals. To ensure flawless berries reach the fermentation process, we hand-sort grapes as soon as we get them into the winery. Our open-top, double-jacketed fermenters allow precise temperature control during "cold soak" periods and primary fermentation -- essential for color, flavor, and tannin extraction. Occasional délestage ("rack & return") aerates the wine. After ratchet basket pressing, we age our wines in French oak barrels for at least 18 months; minimal racking lets wine clarify naturally. Patience, sagacity, gumption, and a balance between both received methods (classic and modern) and ingenuity are foundations for crafting the world-class wines offered by our small, family-run artisanal winery here in the beautiful Walla Walla valley, located beneath the Blue Mountains in eastern Washington

Target Market(s)

Wine drinkers/broken hearts

Industry/Entity Type

Winery

Number of Pages Required

4 page

Font styles to use
Script

Colors

Designer to choose only greyscale colors for use in the design.

Requirements
Must have
• Black roses… From our Walla Walla valley boutique winery here in the Pacific Northwest, we offer a range of premium reds, whites, ice wines, late harvest wines, brandies, grappas, and specialty spirits. We embrace sustainable farming methods on our estate vineyard and source fruit from growers who share our commitment to biodiversity. A great bottle of wine begins with the vine! For our "green wines," we practice innovative eco-friendly techniques, aim for Earth-friendly packaging, and donate a portion of our after-profit proceeds to environmental concerns. Though we appreciate ratings, we're less interested in numbers and more in the approval of our palettes and those of trusted friends, as well as accolades from loyal customers near and far. We handcraft what we hope will become your cult wines, often well into the night, humbled by the calls of barn owls who give our cellar its name.
Nice to have
• Page to list varieties…Tamarack Tokaji, Lanternfall Lambrusco, Cobblemoor Claret

```html
<!DOCTYPE html>
<html lang="en">
<head>
<meta charset="utf-8">
<title>Brindlewick Cellars Winery</title>
<link rel="stylesheet" href="https://fonts.googleapis.com/css2?family=Berkshire+Swash&family=Roboto:wght@400;500;700&family=Tinos&display=swap">
<style>
:root{
  --ink:#2b2f2e;
  --slate:#4d5755;
  --slate-dark:#3f4846;
  --mist:#d9e6e5;
  --paper:#ffffff;
  --text:#555b5a;
  --muted:#7a8180;
  --footer:#252626;
  --rose:#4b5452;
  --script:"Berkshire Swash", cursive;
  --sans:"Roboto", Arial, sans-serif;
}
*{box-sizing:border-box;margin:0;padding:0}
html,body{width:1200px;height:4301px;overflow:hidden}
body{position:relative;background:var(--paper);font-family:var(--sans);color:var(--text)}
.abs{position:absolute}
.script{font-family:var(--script);font-weight:400}
.rule{position:absolute;height:3px;width:70px;background:var(--slate)}
.btn{position:absolute;display:flex;align-items:center;justify-content:center;gap:10px;background:var(--slate);color:#fff;border-radius:24px;font-size:14px;font-weight:700;letter-spacing:.2px}
.btn .arr{width:15px;height:15px;border-radius:50%;background:#fff;display:flex;align-items:center;justify-content:center}
.rose{position:absolute;border-radius:50%;background:radial-gradient(circle at 45% 45%,#6a7472 0%,var(--rose) 45%,rgba(60,68,66,0) 72%)}
.photo{position:absolute}

/* header */
.site-header{position:absolute;left:0;top:0;width:1200px;height:90px;background:#fff}
.logo{position:absolute;font-family:var(--script);color:var(--ink);line-height:1}
.nav{position:absolute;top:35px;font-size:14px;font-weight:700;color:var(--ink)}
.nav-sep{position:absolute;top:35px;font-size:14px;color:var(--ink)}
.search{position:absolute;left:1048px;top:25px;width:40px;height:40px;border-radius:50%;background:#e6e6e6;display:flex;align-items:center;justify-content:center}

/* hero */
.hero{position:absolute;left:0;top:90px;width:1200px;height:640px;background:linear-gradient(100deg,#3e4140 0%,#6b6f6e 40%,#9a9d9c 62%,#555958 100%)}
.hero h2{position:absolute;left:113px;top:190px;font-size:34px;color:#fff}
.hero h1{position:absolute;left:113px;top:235px;font-size:56px;color:#fff;white-space:nowrap}
.hero p{position:absolute;left:113px;top:318px;width:490px;font-family:"Tinos",serif;font-size:18px;line-height:28px;color:#fff}

/* about */
.about-copy{position:absolute;left:112px;top:890px;width:460px;font-size:15px;line-height:25.7px;text-align:justify}

/* wine */
.wine{position:absolute;left:0;top:1310px;width:1200px;height:622px;background:var(--mist)}
.section-title{position:absolute;left:0;width:1200px;text-align:center;font-size:40px;color:var(--ink)}
.wine-item{position:absolute;top:164px;width:300px;text-align:center}
.wine-ring{width:220px;height:220px;margin:0 auto;border-radius:50%;border:2px dotted #3d4443;display:flex;align-items:center;justify-content:center;background:var(--mist)}
.wine-ring .photo{position:static;width:196px;height:196px;border-radius:50%;border:4px solid #fff}
.wine-item h3{margin-top:28px;font-size:17px;font-weight:700;color:var(--text)}
.wine-item p{margin-top:12px;font-size:14px;line-height:24px;color:var(--muted)}

/* feature */
.feature-card{position:absolute;left:509px;top:2094px;width:573px;height:402px;background:#fff;box-shadow:0 4px 24px rgba(0,0,0,.12)}
.feature-card h2{position:absolute;left:109px;top:38px;font-size:38px;line-height:38px;color:var(--ink)}
.feature-card p{position:absolute;left:109px;top:132px;width:414px;font-size:14px;line-height:25.7px;text-align:justify;color:var(--muted)}

/* testimonials */
.testimonials{position:absolute;left:0;top:2571px;width:1200px;height:643px;background:var(--slate)}
.t-card{position:absolute;top:219px;width:459px;height:195px;background:#fff;border-radius:3px}
.t-card::after{content:"";position:absolute;left:36px;bottom:-16px;border-left:14px solid transparent;border-right:14px solid transparent;border-top:16px solid #fff}
.t-card p{position:absolute;left:22px;top:68px;width:415px;font-size:13.5px;line-height:23px;text-align:justify;color:var(--muted)}
.t-author{position:absolute;top:440px;display:flex;align-items:center;gap:14px;color:#fff}
.avatar{width:54px;height:54px;border-radius:50%;background:#d5d9d8;border:3px solid #fff}
.t-author strong{display:block;font-size:17px;font-weight:500}
.t-author span{font-size:14px;color:#e3e6e5}
.dots{position:absolute;top:2572px}

/* events */
.event{position:absolute;left:584px;width:520px;height:100px}
.date{position:absolute;left:0;top:0;width:92px;height:94px;border:2px solid var(--slate);border-radius:8px;overflow:hidden;text-align:center;background:#fff}
.date b{display:block;background:var(--slate);color:#fff;font-size:16px;font-weight:500;height:38px;line-height:38px}
.date i{display:block;font-style:normal;font-size:34px;font-weight:500;color:var(--slate);line-height:52px}
.event h4{position:absolute;left:125px;top:0;font-size:13px;font-weight:700;color:#333}
.meta{position:absolute;left:125px;top:26px;font-size:13px;font-weight:700;color:#444;display:flex;gap:30px}
.meta span{display:flex;align-items:center;gap:12px}
.event p{position:absolute;left:125px;top:54px;width:375px;font-size:13px;line-height:16px;color:#444}

/* footer */
.site-footer{position:absolute;left:0;top:3890px;width:1200px;height:411px;background:var(--footer);color:#fff}
.f-title{position:absolute;top:50px;font-size:14px;font-weight:700}
.f-rule{position:absolute;top:75px;height:2px;width:135px;background:#666}
.f-link{position:absolute;font-size:14px;display:flex;align-items:center;gap:14px}
.f-link .dot{width:14px;height:14px;border-radius:50%;background:#fff;display:flex;align-items:center;justify-content:center}
.f-contact{position:absolute;left:606px;font-size:14px;line-height:20px;display:flex;gap:14px;width:230px}
.field{position:absolute;left:883px;width:205px;background:#fff;border-radius:12px;font-size:10px;color:#999;padding:7px 14px}
.legal{position:absolute;top:4258px;font-size:12px;color:#fff}
</style>
</head>
<body>

<header class="site-header">
  <div class="logo" style="left:112px;top:24px;font-size:36px">Brindlewick Cellars</div>
  <span class="nav" style="left:556px">HOME</span>
  <span class="nav-sep" style="left:633px">|</span>
  <span class="nav" style="left:672px">WINE</span>
  <span class="nav-sep" style="left:744px">|</span>
  <span class="nav" style="left:782px">EVENTS</span>
  <span class="nav-sep" style="left:873px">|</span>
  <span class="nav" style="left:911px">CONTACT US</span>
  <div class="search"><svg width="14" height="14" viewBox="0 0 14 14"><circle cx="6" cy="6" r="4.2" fill="none" stroke="#222" stroke-width="2"/><path d="M9 9l3.5 3.5" stroke="#222" stroke-width="2"/></svg></div>
</header>

<section class="hero">
  <div class="photo" role="img" aria-label="Black and white photo of a bride and groom toasting with champagne flutes" style="left:0;top:0;width:1200px;height:640px;background:linear-gradient(100deg,rgba(40,42,41,.7) 0%,rgba(40,42,41,.35) 45%,rgba(0,0,0,0) 70%)"></div>
  <h2 class="script">Welcome To</h2>
  <h1 class="script">Brindlewick Cellars</h1>
  <p>Lorem ipsum dolor sit amet, consectetur adipiscing elit, sed do eiusmod tempor incididunt ut labore et dolore magna aliqua.</p>
  <div class="btn" style="left:113px;top:392px;width:156px;height:40px;background:rgba(80,84,83,.85)">READ MORE <span class="arr"><svg width="8" height="8" viewBox="0 0 8 8"><path d="M2 1l3 3-3 3" stroke="#4d5755" stroke-width="1.8" fill="none"/></svg></span></div>
  <svg class="abs" style="left:0;top:600px" width="1200" height="40" viewBox="0 0 1200 40" preserveAspectRatio="none"><path d="M0 22 L60 14 L120 24 L180 12 L240 20 L300 8 L360 18 L430 10 L500 22 L570 12 L640 20 L700 6 L770 16 L840 10 L900 22 L960 8 L1030 18 L1090 12 L1150 20 L1200 14 L1200 40 L0 40Z" fill="#fff"/></svg>
</section>
<div class="rose" role="img" aria-label="Black rose illustration" style="left:-50px;top:690px;width:180px;height:180px"></div>

<section>
  <h2 class="abs script" style="left:112px;top:805px;font-size:42px;color:var(--ink)">About Us</h2>
  <div class="rule" style="left:112px;top:867px"></div>
  <p class="about-copy">We employ a combination of modern techniques and old world traditions, practicing both the cuvee and "field blending" methods, to create a range of distinctive varietals. To ensure flawless berries reach the fermentation process, we hand-sort grapes as soon as we get them into the winery. Our open-top, double-jacketed fermenters allow precise temperature control during "cold soak" periods and primary fermentation – essential for color, flavor, and tannin extraction. Occasional délestage ("rack &amp; return") aerates the wine. After ratchet basket pressing, we age our wines in French oak barrels for at least 18 months; minimal racking lets wine</p>
  <div class="btn" style="left:112px;top:1175px;width:155px;height:46px">READ MORE <span class="arr"><svg width="8" height="8" viewBox="0 0 8 8"><path d="M2 1l3 3-3 3" stroke="#4d5755" stroke-width="1.8" fill="none"/></svg></span></div>
  <svg class="abs" style="left:630px;top:818px" width="460" height="390"><path d="M20 4 L458 20 L450 386 L4 382Z" fill="var(--slate)"/></svg>
  <div class="photo" role="img" aria-label="Black and white photo of guests clinking wine glasses" style="left:651px;top:838px;width:421px;height:364px;background:linear-gradient(135deg,#9c9f9e,#5c605f 55%,#3c3f3e)"></div>
  <div class="rose" role="img" aria-label="Black rose illustration" style="left:1010px;top:1110px;width:240px;height:220px"></div>
  <div class="rose" role="img" aria-label="Rose leaves illustration" style="left:880px;top:1210px;width:140px;height:100px;opacity:.7"></div>
</section>

<section class="wine">
  <h2 class="section-title script" style="top:60px">Wine</h2>
  <div class="rule" style="left:565px;top:116px"></div>
  <div class="wine-item" style="left:109px">
    <div class="wine-ring"><div class="photo" role="img" aria-label="Photo of glasses of white wine being raised" style="background:linear-gradient(135deg,#c9cccb,#6d7170)"></div></div>
    <h3>Tamarack Tokaji</h3>
    <p>Lorem ipsum dolor sit consectetur adipiscing sed do eiusmod tempor incididunt ut labore et dolore magna aliquaed enime minim veniam, quis nostrud exercitation.</p>
  </div>
  <div class="wine-item" style="left:449px">
    <div class="wine-ring"><div class="photo" role="img" aria-label="Photo of red wine being poured into a glass" style="background:linear-gradient(135deg,#7a7e7d,#2e3130)"></div></div>
    <h3>Lanternfall Lambrusco</h3>
    <p>Lorem ipsum dolor sit consectetur adipiscing sed do eiusmod tempor incididunt ut labore et dolore magna aliquaed enime minim veniam, quis nostrud exercitation.</p>
  </div>
  <div class="wine-item" style="left:790px">
    <div class="wine-ring"><div class="photo" role="img" aria-label="Photo of wine poured from a bottle into a glass" style="background:linear-gradient(135deg,#4a4d4c,#1f2120)"></div></div>
    <h3>Cobblemoor Claret</h3>
    <p>Lorem ipsum dolor sit consectetur adipiscing sed do eiusmod tempor incididunt ut labore et dolore magna aliquaed enime minim veniam, quis nostrud exercitation.</p>
  </div>
</section>

<section>
  <div class="rose" role="img" aria-label="Black rose illustration" style="left:-20px;top:1890px;width:200px;height:150px"></div>
  <div class="abs" style="left:103px;top:2028px;width:441px;height:326px;border:4px solid var(--slate)"></div>
  <div class="photo" role="img" aria-label="Black and white photo of a bride holding a bouquet and a champagne flute beside the groom" style="left:120px;top:2045px;width:453px;height:342px;border:6px solid #fff;box-shadow:0 3px 14px rgba(0,0,0,.2);background:linear-gradient(120deg,#5a5e5d,#a9acab 55%,#e2e3e3)"></div>
  <svg class="abs" style="left:437px;top:2388px" width="74" height="54"><defs><pattern id="dotgrid" width="4" height="4" patternUnits="userSpaceOnUse"><circle cx="1" cy="1" r=".8" fill="#777"/></pattern></defs><rect width="74" height="54" fill="url(#dotgrid)"/></svg>
  <div class="feature-card">
    <h2 class="script">Must have this<br>content in the site</h2>
    <div class="rule" style="left:109px;top:117px"></div>
    <p>Black roses... From our Walla Walla valley boutique winery here in the Pacific Northwest, we offer a range of premium reds, whites, ice wines, late harvest wines, brandies, grappas, and specialty spirits. We embrace sustainable farming methods on our estate vineyard and source fruit from growers who share our commitment to biodiversity. A great bottle of wine begins with the vine! For our "green wines," we practice innovative.</p>
    <div class="btn" style="left:109px;top:320px;width:145px;height:44px;font-size:13px">LEARN MORE <span class="arr"><svg width="8" height="8" viewBox="0 0 8 8"><path d="M2 1l3 3-3 3" stroke="#4d5755" stroke-width="1.8" fill="none"/></svg></span></div>
  </div>
  <div class="rose" role="img" aria-label="Black rose illustration" style="left:990px;top:2470px;width:230px;height:160px"></div>
</section>

<section class="testimonials">
  <svg class="abs" style="left:0;top:-18px" width="1200" height="40" viewBox="0 0 1200 40" preserveAspectRatio="none"><path d="M0 18 L70 10 L140 22 L210 8 L290 20 L360 12 L440 24 L520 10 L600 20 L680 6 L760 18 L840 12 L920 22 L1000 10 L1080 20 L1140 8 L1200 16 L1200 40 L0 40Z" fill="var(--slate)"/></svg>
  <h2 class="section-title script" style="top:105px;color:#fff">Our Testimonials</h2>
  <div class="rule" style="left:565px;top:165px;background:#fff"></div>
  <div class="t-card" style="left:122px">
    <svg class="abs" style="left:28px;top:20px" width="48" height="34" viewBox="0 0 48 34"><path d="M2 34V18C2 8 8 2 18 0l2 5c-6 2-8 6-8 11h8v18Z M26 34V18C26 8 32 2 42 0l2 5c-6 2-8 6-8 11h8v18Z" fill="var(--slate)"/></svg>
    <p>Lorem ipsum dolor sit amet, consectetur adipiscing elit, sed do eiusmod tempor incididunt ut labore et dolore magna aliqua. Ut enim ad minim veniam, quis nostrud exercitation ullamco laboris nisi ut aliquip ex ea commodo consequat. Duis autedolor in reprehenderit in voluptate velit esse cillum dolored.</p>
  </div>
  <div class="t-card" style="left:619px">
    <svg class="abs" style="left:28px;top:20px" width="48" height="34" viewBox="0 0 48 34"><path d="M2 34V18C2 8 8 2 18 0l2 5c-6 2-8 6-8 11h8v18Z M26 34V18C26 8 32 2 42 0l2 5c-6 2-8 6-8 11h8v18Z" fill="var(--slate)"/></svg>
    <p>Lorem ipsum dolor sit amet, consectetur adipiscing elit, sed do eiusmod tempor incididunt ut labore et dolore magna aliqua. Ut enim ad minim veniam, quis nostrud exercitation ullamco laboris nisi ut aliquip ex ea commodo consequat. Duis autedolor in reprehenderit in voluptate velit esse cillum dolored.</p>
  </div>
  <div class="t-author" style="left:145px"><div class="avatar" role="img" aria-label="Customer portrait"></div><div><strong>Marlow Penn</strong><span>Lorem ipsum dolor</span></div></div>
  <div class="t-author" style="left:643px"><div class="avatar" role="img" aria-label="Customer portrait"></div><div><strong>Marlow Penn</strong><span>Lorem ipsum dolor</span></div></div>
  <svg class="abs" style="left:574px;top:524px" width="52" height="16"><circle cx="8" cy="8" r="6" fill="none" stroke="#fff" stroke-width="1.5"/><circle cx="26" cy="8" r="6" fill="#fff"/><circle cx="44" cy="8" r="6" fill="none" stroke="#fff" stroke-width="1.5"/></svg>
  <svg class="abs" style="left:0;top:623px" width="1200" height="40" viewBox="0 0 1200 40" preserveAspectRatio="none"><path d="M0 0 L1200 0 L1200 20 L1130 12 L1060 24 L980 10 L900 22 L820 8 L740 20 L660 12 L580 24 L500 10 L420 22 L340 8 L260 20 L180 12 L100 24 L40 10 L0 18Z" fill="var(--slate)"/></svg>
</section>
<div class="rose" role="img" aria-label="Black rose illustration" style="left:-40px;top:3200px;width:190px;height:190px"></div>

<section>
  <h2 class="section-title script" style="top:3290px">Latest Events</h2>
  <div class="rule" style="left:565px;top:3358px"></div>
  <div class="photo" role="img" aria-label="Black and white photo of wedding guests raising glasses at an outdoor table under string lights" style="left:112px;top:3414px;width:425px;height:354px;background:linear-gradient(160deg,#6f7372,#b8bbba 45%,#4a4d4c)"></div>
  <div class="event" style="top:3414px">
    <div class="date"><b>JAN</b><i>18</i></div>
    <h4>LOREM IPSUM DOLOR SIT AMET CONSECTETUR</h4>
    <div class="meta"><span><svg width="12" height="13" viewBox="0 0 12 13"><circle cx="6" cy="3.5" r="3" fill="#555"/><path d="M0 13c0-4 2.5-6 6-6s6 2 6 6Z" fill="#555"/></svg>JOHN DOE</span><span><svg width="10" height="13" viewBox="0 0 10 13"><path d="M5 0a5 5 0 0 1 5 5c0 3-5 8-5 8S0 8 0 5a5 5 0 0 1 5-5Z" fill="#555"/><circle cx="5" cy="5" r="1.8" fill="#fff"/></svg>Lorem Ipsum Dolor , USA</span></div>
    <p>Sed ut perspiciatis unde omnis iste natus error sivoluptatem accusantium doloremque laudantium.</p>
  </div>
  <div class="event" style="top:3544px">
    <div class="date"><b>JAN</b><i>19</i></div>
    <h4>LOREM IPSUM DOLOR SIT AMET CONSECTETUR</h4>
    <div class="meta"><span><svg width="12" height="13" viewBox="0 0 12 13"><circle cx="6" cy="3.5" r="3" fill="#555"/><path d="M0 13c0-4 2.5-6 6-6s6 2 6 6Z" fill="#555"/></svg>JOHN DOE</span><span><svg width="10" height="13" viewBox="0 0 10 13"><path d="M5 0a5 5 0 0 1 5 5c0 3-5 8-5 8S0 8 0 5a5 5 0 0 1 5-5Z" fill="#555"/><circle cx="5" cy="5" r="1.8" fill="#fff"/></svg>Lorem Ipsum Dolor , USA</span></div>
    <p>Sed ut perspiciatis unde omnis iste natus error sivoluptatem accusantium doloremque laudantium.</p>
  </div>
  <div class="event" style="top:3674px">
    <div class="date"><b>JAN</b><i>20</i></div>
    <h4>LOREM IPSUM DOLOR SIT AMET CONSECTETUR</h4>
    <div class="meta"><span><svg width="12" height="13" viewBox="0 0 12 13"><circle cx="6" cy="3.5" r="3" fill="#555"/><path d="M0 13c0-4 2.5-6 6-6s6 2 6 6Z" fill="#555"/></svg>JOHN DOE</span><span><svg width="10" height="13" viewBox="0 0 10 13"><path d="M5 0a5 5 0 0 1 5 5c0 3-5 8-5 8S0 8 0 5a5 5 0 0 1 5-5Z" fill="#555"/><circle cx="5" cy="5" r="1.8" fill="#fff"/></svg>Lorem Ipsum Dolor , USA</span></div>
    <p>Sed ut perspiciatis unde omnis iste natus error sivoluptatem accusantium doloremque laudantium.</p>
  </div>
  <div class="rose" role="img" aria-label="Black rose illustration" style="left:1000px;top:3660px;width:240px;height:220px"></div>
</section>

<footer class="site-footer">
  <svg class="abs" style="left:0;top:-22px" width="1200" height="40" viewBox="0 0 1200 40" preserveAspectRatio="none"><path d="M0 20 L80 10 L160 24 L240 12 L320 22 L400 8 L480 20 L560 12 L640 24 L720 10 L800 20 L880 6 L960 18 L1040 10 L1120 22 L1200 12 L1200 40 L0 40Z" fill="var(--footer)"/></svg>
  <div class="logo" style="left:107px;top:62px;font-size:36px;color:#fff;width:220px;line-height:1.1">Brindlewick Cellars</div>

  <div class="f-title" style="left:396px">Quick Links</div><div class="f-rule" style="left:396px"></div>
  <div class="f-link" style="left:396px;top:106px"><span class="dot"><svg width="6" height="6" viewBox="0 0 6 6"><path d="M1.5 0.5l3 2.5-3 2.5" stroke="#252626" stroke-width="1.4" fill="none"/></svg></span>Home</div>
  <div class="f-link" style="left:396px;top:147px"><span class="dot"><svg width="6" height="6" viewBox="0 0 6 6"><path d="M1.5 0.5l3 2.5-3 2.5" stroke="#252626" stroke-width="1.4" fill="none"/></svg></span>Wine</div>
  <div class="f-link" style="left:396px;top:190px"><span class="dot"><svg width="6" height="6" viewBox="0 0 6 6"><path d="M1.5 0.5l3 2.5-3 2.5" stroke="#252626" stroke-width="1.4" fill="none"/></svg></span>Contact</div>

  <div class="f-title" style="left:606px">Contact Us</div><div class="f-rule" style="left:606px"></div>
  <div class="f-contact" style="top:106px"><svg width="12" height="16" viewBox="0 0 12 16"><path d="M6 1a5 5 0 0 1 5 5c0 3.5-5 9-5 9S1 9.5 1 6a5 5 0 0 1 5-5Z" fill="none" stroke="#fff" stroke-width="1.3"/><circle cx="6" cy="6" r="1.8" fill="#fff"/></svg><span>504 Lorem ipsum dolor sit amet, consectetur ad</span></div>
  <div class="f-contact" style="top:160px"><svg width="14" height="12" viewBox="0 0 14 12"><rect x="1" y="2" width="12" height="8" fill="none" stroke="#fff" stroke-width="1.2"/><path d="M1 2l6 5 6-5" fill="none" stroke="#fff" stroke-width="1.2"/></svg><span>info@brindlewickcellars.com</span></div>
  <div class="f-contact" style="top:204px"><svg width="14" height="14" viewBox="0 0 14 14"><path d="M3 1l2.5 3-1.5 1.5c1 2 2.5 3.5 4.5 4.5L10 8.5l3 2.5-1.5 2C6 13 1 8 1 2.5Z" fill="none" stroke="#fff" stroke-width="1.2"/></svg><span>+1 555 010 2040</span></div>
  <div class="f-contact" style="top:246px"><svg width="14" height="14" viewBox="0 0 14 14"><rect x="1" y="3" width="12" height="10" fill="none" stroke="#fff" stroke-width="1.2"/><rect x="4" y="1" width="4" height="12" fill="none" stroke="#fff" stroke-width="1.2"/></svg><span>+1 555 010 7788</span></div>

  <div class="f-title" style="left:883px">Get In Touch</div><div class="f-rule" style="left:883px"></div>
  <div class="field" style="top:112px;height:30px">Name*</div>
  <div class="field" style="top:152px;height:30px">Email*</div>
  <div class="field" style="top:190px;height:55px">Message*</div>
  <div class="btn" style="left:883px;top:254px;width:137px;height:33px;font-size:13px">SUBMIT NOW</div>

  <div class="abs" style="left:0;top:340px;width:1200px;height:1px;background:#3a3b3b"></div>
  <div class="legal" style="left:112px;top:368px">© 2024 Brindlewick Cellars. | All Rights Reserved</div>
  <div class="legal" style="left:763px;top:368px">Privacy Policy &nbsp;| &nbsp;Cookie Policy &nbsp;| &nbsp;Terms Of Services</div>
</footer>

</body>
</html>
```